Home Staging Company needs business card design

We're a home staging company called Brightly Settled Home Staging. We would like a business card design that includes aqua and gray. Our current logo of house within chair is fine but I find we almost always use the logo in one color. I'll upload images of front and back of our current card and our logo. Note that we have dropped "Solutions" from our company name and don't want to include it on the card.

Target Market(s)

Realtors and homeowners - people interested in selling their homes

Contact Information for Business Card

Marisol Thistlewood
Brightly Settled Home Staging
757-555-0193
www.brightlysettled.com
marisol@brightlysettled.com

Font styles to use
Serif
Script

Requirements
Must have
• My logo and contact details
• UPDATE***
• I forgot to say that the company name should be included on the front of the card somehow.

```html
<!DOCTYPE html>
<html lang="en">
<head>
<meta charset="utf-8">
<title>Brightly Settled Home Staging – Business Card</title>
<link rel="stylesheet" href="https://fonts.googleapis.com/css2?family=Roboto:wght@300;400&family=Questrial&family=Playfair+Display:wght@400&display=swap">
<style>
  :root {
    --page-bg: #b9b9b9;
    --card-bg: #373b40;
    --card-accent-shape: #40454a;
    --aqua: #4ca6b1;
    --text-light: #eef0f1;
    --text-soft: #d9dcde;
    --shadow: rgba(0, 0, 0, 0.28);
  }
  * { box-sizing: border-box; margin: 0; padding: 0; }
  html, body {
    width: 1200px;
    height: 576px;
    overflow: hidden;
    background: var(--page-bg);
  }
  .canvas {
    position: relative;
    width: 1200px;
    height: 576px;
  }
  .card {
    position: absolute;
    top: 138px;
    width: 484px;
    height: 294px;
    background: var(--card-bg);
    border-radius: 12px;
    overflow: hidden;
    box-shadow: 0 3px 6px var(--shadow);
  }
  .card--front { left: 82px; }
  .card--back { left: 602px; }

  .backdrop-disc {
    position: absolute;
    width: 304px;
    height: 304px;
    border-radius: 50%;
    background: var(--card-accent-shape);
  }
  .card--front .backdrop-disc { left: 350px; top: -26px; }
  .card--back .backdrop-disc { left: -170px; top: -26px; }

  .person {
    position: absolute;
    left: 26px;
    top: 34px;
  }
  .person__name {
    font-family: "Roboto", sans-serif;
    font-weight: 300;
    font-size: 19.5px;
    color: var(--text-light);
    letter-spacing: 0.2px;
  }
  .person__surname { color: var(--aqua); }
  .person__role {
    margin-top: 4px;
    font-family: "Questrial", sans-serif;
    font-size: 11px;
    color: var(--text-soft);
  }

  .contacts {
    position: absolute;
    left: 27px;
    top: 101px;
    list-style: none;
  }
  .contacts__item {
    display: flex;
    align-items: center;
    height: 17px;
    font-family: "Questrial", sans-serif;
    font-size: 12.5px;
    color: var(--text-light);
  }
  .contacts__icon {
    width: 11px;
    height: 11px;
    margin-right: 12px;
    fill: var(--aqua);
    flex: none;
  }
  .contacts__highlight { color: var(--aqua); }

  .brand {
    position: absolute;
    display: flex;
    align-items: center;
    gap: 9px;
  }
  .card--front .brand { left: 26px; top: 222px; }
  .card--back .brand { left: 222px; top: 219px; }
  .brand__dot {
    width: 36px;
    height: 36px;
    border-radius: 50%;
    background: var(--aqua);
    flex: none;
  }
  .brand__name {
    font-family: "Playfair Display", serif;
    font-weight: 400;
    font-size: 16px;
    line-height: 1.15;
    color: var(--aqua);
    width: 170px;
  }
</style>
</head>
<body>
<main class="canvas">

  <section class="card card--front" aria-label="Card front">
    <div class="backdrop-disc" aria-hidden="true"></div>

    <div class="person">
      <h1 class="person__name">Marisol <span class="person__surname">Thistlewood</span></h1>
      <p class="person__role">Managing Director</p>
    </div>

    <ul class="contacts">
      <li class="contacts__item">
        <svg class="contacts__icon" viewBox="0 0 12 12" aria-hidden="true">
          <path d="M1 3.2C1 2 2 1.5 6 1.5S11 2 11 3.2V4.4H8.4V3.4H3.6V4.4H1Z"/>
          <path d="M2.6 5.2H9.4L10.6 10.5H1.4Z"/>
        </svg>
        757-555-0193
      </li>
      <li class="contacts__item">
        <svg class="contacts__icon" viewBox="0 0 12 12" aria-hidden="true">
          <path d="M6 0.8A5.2 5.2 0 1 0 6 11.2A5.2 5.2 0 1 0 6 0.8ZM6 2.1C6.6 2.6 7.1 3.6 7.3 5.3H4.7C4.9 3.6 5.4 2.6 6 2.1ZM4.7 6.7H7.3C7.1 8.4 6.6 9.4 6 9.9C5.4 9.4 4.9 8.4 4.7 6.7ZM2.2 5.3C2.4 4.1 3 3.1 3.9 2.5C3.6 3.3 3.4 4.2 3.3 5.3ZM8.7 5.3C8.6 4.2 8.4 3.3 8.1 2.5C9 3.1 9.6 4.1 9.8 5.3ZM2.2 6.7H3.3C3.4 7.8 3.6 8.7 3.9 9.5C3 8.9 2.4 7.9 2.2 6.7ZM8.7 6.7H9.8C9.6 7.9 9 8.9 8.1 9.5C8.4 8.7 8.6 7.8 8.7 6.7Z"/>
        </svg>
        <span>www.<span class="contacts__highlight">brightlysettled</span>.com</span>
      </li>
      <li class="contacts__item">
        <svg class="contacts__icon" viewBox="0 0 12 12" aria-hidden="true">
          <path d="M0.8 2.5H11.2V3.1L6 6.7L0.8 3.1Z"/>
          <path d="M0.8 4.3L6 7.9L11.2 4.3V9.5H0.8Z"/>
        </svg>
        marisol@brightlysettled.com
      </li>
    </ul>

    <div class="brand">
      <span class="brand__dot" aria-hidden="true"></span>
      <span class="brand__name">Brightly Settled Home Staging</span>
    </div>
  </section>

  <section class="card card--back" aria-label="Card back">
    <div class="backdrop-disc" aria-hidden="true"></div>
    <div class="brand">
      <span class="brand__dot" aria-hidden="true"></span>
      <span class="brand__name">Brightly Settled Home Staging</span>
    </div>
  </section>

</main>
</body>
</html>
```